Young, dynamic furniture company needs a new business card design

We require a new business card design for our modern furniture company which supplies furniture and appliances to the property and development market.
Oakridge Interiors has become one of the leading furniture & appliance suppliers to the property market withing London. With over 10 years experience, we have increased our business to supply not only private landlords and managing agents, but also property developers, housing associations and local councils.
We offer not only a complete range of furniture which includes beds, wardrobes, dining sets and sofas, but also a high quality, full delivery and assembly service to help you with all our furnishing needs.

Target Market(s)

Private landlords, estate agents, letting agents, property management companies

Industry/Entity Type

Business

Contact Information for Business Card

Name,
Title,
Address,
Mobile,
Telephone,
Fax, Website, email address

Font styles to use
Sans Serif

Colors
3176b5
0555a3
85abd2
cfdeed

Requirements
Must have
• All the above information for each of our staff, along with our logo

```html
<!DOCTYPE html>
<html lang="en">
<head>
<meta charset="utf-8">
<title>Oakridge Interiors – Business Card</title>
<link rel="stylesheet" href="https://fonts.googleapis.com/css2?family=Montserrat:wght@400;700&family=Roboto+Condensed:wght@300;400&display=swap">
<style>
  :root {
    --backdrop: #2b2b2d;
    --card-front: #27336f;
    --card-back: #213a6e;
    --brand-light: #cfdeed;
    --brand-mid: #3176b5;
    --ink: #ffffff;
  }
  html, body {
    margin: 0;
    width: 1189px;
    height: 1200px;
    overflow: hidden;
    background: var(--backdrop);
  }
  .card {
    position: absolute;
    left: 172px;
    width: 855px;
    height: 487px;
    border-radius: 20px;
    color: var(--ink);
  }
  .card--front { top: 68px; background: var(--card-front); }
  .card--back { top: 627px; background: var(--card-back); }

  .brand {
    position: absolute;
    text-align: center;
    font-family: "Roboto Condensed", sans-serif;
    font-weight: 300;
  }
  .brand__mark {
    display: block;
    margin: 0 auto;
    background: var(--brand-mid);
    border: 5px solid var(--ink);
    border-radius: 6px;
  }
  .brand__name {
    display: block;
    white-space: nowrap;
    text-transform: uppercase;
    letter-spacing: 0.5px;
  }
  .brand__tagline {
    display: block;
    white-space: nowrap;
    text-transform: uppercase;
  }

  .card--front .brand { left: 0; right: 0; top: 150px; }
  .card--front .brand__mark { width: 110px; height: 110px; margin-bottom: 34px; }
  .card--front .brand__name { font-size: 36px; line-height: 40px; }
  .card--front .brand__tagline { font-size: 18.5px; line-height: 24px; }

  .card--back .brand { left: 40px; width: 370px; top: 140px; }
  .card--back .brand__mark { width: 96px; height: 96px; margin-bottom: 44px; }
  .card--back .brand__name { font-size: 32px; line-height: 36px; }
  .card--back .brand__tagline { font-size: 17px; line-height: 22px; }

  .divider {
    position: absolute;
    left: 418px;
    top: 91px;
    width: 1px;
    height: 302px;
    background: var(--brand-light);
    opacity: 0.7;
  }

  .contact {
    position: absolute;
    left: 465px;
    top: 84px;
    font-family: "Montserrat", sans-serif;
    font-weight: 400;
  }
  .contact__name {
    margin: 0;
    font-size: 30px;
    font-weight: 700;
    line-height: 30px;
    text-transform: uppercase;
  }
  .contact__title {
    margin: 0;
    font-size: 21px;
    line-height: 24px;
  }
  .contact__address {
    margin: 31px 0 0;
    font-size: 21.5px;
    line-height: 31px;
    font-style: normal;
  }
  .contact__list {
    list-style: none;
    margin: 6px 0 0;
    padding: 0;
    font-size: 22px;
  }
  .contact__list li {
    display: flex;
    align-items: center;
    height: 29px;
  }
  .contact__icon {
    width: 26px;
    height: 26px;
    margin-right: 8px;
    flex: none;
  }
  .contact__web {
    margin: 14px 0 0;
    font-size: 21.5px;
  }
</style>
</head>
<body>

<section class="card card--front">
  <div class="brand">
    <span class="brand__mark"></span>
    <span class="brand__name">Oakridge Interiors</span>
    <span class="brand__tagline">Trade Furniture Solutions</span>
  </div>
</section>

<section class="card card--back">
  <div class="brand">
    <span class="brand__mark"></span>
    <span class="brand__name">Oakridge Interiors</span>
    <span class="brand__tagline">Trade Furniture Solutions</span>
  </div>

  <div class="divider"></div>

  <div class="contact">
    <h1 class="contact__name">Daniel Hart</h1>
    <p class="contact__title">Maneger</p>
    <address class="contact__address">Your Address,2nd Ste<br>Millbrook, Avonshire 4821, UK</address>
    <ul class="contact__list">
      <li>
        <svg class="contact__icon" viewBox="0 0 26 26" aria-hidden="true"><rect width="26" height="26" rx="3" fill="#fff"/><path d="M9 5c1 0 2 3 2 4s-1.5 1.5-1.5 2.5 2.5 4.5 3.5 4.5 1.5-1.5 2.5-1.5 3.5 1.5 3.5 2.5-1.5 3-3.5 3C11 20.5 6 14 6 9c0-2 2-4 3-4z" fill="#213a6e"/></svg>
        123 456 7890
      </li>
      <li>
        <svg class="contact__icon" viewBox="0 0 26 26" aria-hidden="true"><rect width="26" height="26" rx="3" fill="#fff"/><rect x="8" y="5" width="10" height="5" fill="#213a6e"/><rect x="5" y="10" width="16" height="8" rx="1.5" fill="#213a6e"/><rect x="8" y="15" width="10" height="6" fill="#213a6e" stroke="#fff" stroke-width="1.2"/></svg>
        123 456 7890
      </li>
      <li>
        <svg class="contact__icon" viewBox="0 0 26 26" aria-hidden="true"><rect width="26" height="26" rx="3" fill="#fff"/><rect x="8" y="4" width="10" height="18" rx="2" fill="#213a6e"/><rect x="10" y="7" width="6" height="5" fill="#fff"/></svg>
        123 456 7890
      </li>
      <li>
        <svg class="contact__icon" viewBox="0 0 26 26" aria-hidden="true"><rect width="26" height="26" rx="3" fill="#fff"/><rect x="4" y="7" width="18" height="12" fill="none" stroke="#213a6e" stroke-width="2"/><path d="M4 7l9 7 9-7M4 19l7-6M22 19l-7-6" fill="none" stroke="#213a6e" stroke-width="1.6"/></svg>
        your@yourcompany.com
      </li>
    </ul>
    <p class="contact__web">www.yourcompany.com</p>
  </div>
</section>

</body>
</html>
```